Upmarket Dessert Lounge needs a Business Card Design

We are an upmarket dessert lounge needing a business card to match our image.

We want something that is simple yet beautiful, feminine, classy, sophisticated and elegant. We want it to stand out and don't mind if it is bold.

The design should include our logo and colours of red or maroon with gold highlights. We don't mind if black is used.

Marlow & Quince

Target Market(s)

For those who like to indulge or treat themselves and give in to their temptations on good quality desserts.

Industry/Entity Type

Business

Requirements
Must have
• Must include our logo and our name

Marlow & Quince

M & Q

```html
<!DOCTYPE html>
<html lang="en">
<head>
<meta charset="utf-8">
<title>Marlow &amp; Quince Business Card</title>
<link href="https://fonts.googleapis.com/css2?family=Open+Sans:wght@400;600;700&display=swap" rel="stylesheet">
<style>
  :root {
    --backdrop: #d9d9db;
    --card-black: #000000;
    --maroon: #7a1517;
    --gold: #f5cf94;
    --white: #ffffff;
  }
  * { margin: 0; padding: 0; box-sizing: border-box; }
  html, body { width: 956px; height: 1200px; overflow: hidden; }
  body {
    position: relative;
    background: var(--backdrop);
    font-family: "Open Sans", Arial, sans-serif;
  }
  .card {
    position: absolute;
    background: var(--card-black);
    border-radius: 28px;
    overflow: hidden;
  }
  .card-front { left: 78px; top: 96px; width: 799px; height: 455px; }
  .card-back {
    left: 74px; top: 632px; width: 797px; height: 456px;
    display: flex; align-items: center; justify-content: center;
  }
  .swoosh { position: absolute; inset: 0; width: 100%; height: 100%; }
  .brand-name {
    position: absolute;
    left: 0; width: 700px;
    top: 72px; height: 134px;
    display: flex; align-items: center; justify-content: center;
    color: var(--gold);
    font-weight: 600;
    font-size: 48px;
    letter-spacing: 1px;
    white-space: nowrap;
  }
  .contact {
    position: absolute;
    left: 0; width: 700px;
    text-align: center;
    color: var(--white);
    font-size: 19.5px;
    line-height: 1;
    white-space: nowrap;
  }
  .contact b { font-weight: 700; }
  .contact .sep { margin: 0 8px; }
  .person { top: 279px; font-size: 23.5px; color: var(--gold); }
  .phones { top: 326px; }
  .web { top: 369px; }
  .address { top: 410px; }
  .monogram {
    color: var(--gold);
    font-weight: 600;
    font-size: 140px;
    line-height: 1;
    white-space: nowrap;
    margin-left: 8px;
  }
</style>
</head>
<body>
  <section class="card card-front">
    <svg class="swoosh" viewBox="0 0 799 455" aria-hidden="true">
      <path d="M552,0 C720,60 800,250 672,455 L799,455 L799,0 Z" fill="var(--maroon)"/>
      <path d="M598,0 C745,75 795,280 684,455 L706,455 C795,290 775,110 662,0 Z" fill="var(--card-black)"/>
    </svg>
    <div class="brand-name">Marlow &amp; Quince</div>
    <p class="contact person"><b>Your Name -</b> Designation</p>
    <p class="contact phones"><b>p</b> : 123-456-7890<span class="sep">|</span><b>c</b> : 123-456-7890<span class="sep">|</span><b>f</b> : 123-456-7890</p>
    <p class="contact web"><b>e</b> : name@yourwebsite.com<span class="sep">|</span><b>w</b> : www.marlow&amp;quince.com</p>
    <p class="contact address">0000, Street Name, City Name, Country Code.</p>
  </section>

  <section class="card card-back">
    <div class="monogram">M &amp; Q</div>
  </section>
</body>
</html>
```